New B2C website design to help dads be better dads

DadHarbor is a website to help dads be the “best dad you can be.”

We require our website to be designed into a PSD format, no coding necessary.

The general concept is a two-page design. The first page is the login page, the second page is the home page. Once at the home page, rather than navigating to and from different pages, the user will push and pull through different visual and functional layers of the hierarchy. In theory, this should add to the user experience by having a visual anchor of where they are (through layered pagination) as well as improving loading times since the new information should only be a delta in data load versus a brand new page load.

The general look-and-feel we are going for is clean, simple, minimal. This means that the winning design will show us a good eye for web-optimized typography, good use of white (negative) space, and good use of a visually pleasing grid.

We require a total of 6 page "views" plus the landing page. We note that many of the views are similar to one another.
Landing page
Milestone view
Task view
Content view, articles
Content view, products
Search view
What's new view

Please review all of the additional information provided as well as the attachments for examples.

We provide the following websites as good references for:

Typography:
http://example-kelvorn.com/journal/

Use of white space:
http://www.trenvaskit.com/
http://moldrefin.com/

Example for “scrolling” page concept as well as good balance of color, typography, and white space:
http://www.qorbitalmeet.eu/

Please contact us with questions so that we can guide your design effort.
Updates

Hello designers,

The following information is added to help guide the design process:

1.  For the text dialogue below the landing page, please assume the following word count:
"why are we making dad harbor?": 250 words
"who are we?" 200 words
"what's the deal with the penguin logo?" 300 words

For the social media links, please see http://www.gravelplumbs.com/
Notice the floating "social" bar that is always to the right.  This is the concept we are going for, please try to implement this as you see fit. 

Target Market(s)

Fathers of young children ages 0-6 years old.

Industry/Entity Type

Product

Font styles to use
Sans Serif

Requirements
Must have
• Clean lines, minimal design concept

Incorporation of our logo (see attached document)

Header content is static for all views after landing page, see example

This page WILL be responsive, please keep that in mind when designing
The timeline bar should be to the left, with the timeline bar’s “milestones” also being responsive.

Designer is free to suggest font types, but any fonts used must be royalty-free and web-optimized. We request a minimum number of font types as well as fonts that load relatively fast. We reinforce that visually appealing typography is a significant factor in the winning design choice.

While we are not expecting the winning design to include code, please keep in mind that the final implementation needs to be optimized for desktop, tablet, and mobile platforms.

If you are using stock photography that is not generated by you, please provide where/how we can obtain imagery, as well as price.

All custom graphics must be available in original formats; Photoshop/GIMP layered files for layout design, and vector formats for logos, icons and other graphical elements.

Please incorporate “Blue” into design elements as you see fit, as the RGB 67 74 169 Blue is the primary color used in our brand. The complement to this blue is 255 202 0, a brownish orange. Feel free to use this color as well, although please keep it to a lesser amount.

Background color is your choice, do not feel the need to use the grey.
Should not have
• Excessive graphical content such that it affects loading times

Excessive use of too many font types such that it affects loading times

```html
<!DOCTYPE html>
<html lang="en">
<head>
<meta charset="utf-8">
<title>DadHarbor — Home</title>
<link rel="stylesheet" href="https://fonts.googleapis.com/css2?family=PT+Sans:wght@400;700&family=Roboto+Slab:wght@300;400&display=swap">
<style>
  :root {
    --brand-blue: #434aa9;
    --brand-gold: #d9a21b;
    --accent-yellow: #f5c42a;
    --page-bg: #f7f7f7;
    --panel-bg: #ffffff;
    --rule: #dcdcdc;
    --text-dark: #444444;
    --text-muted: #777777;
    --text-light: #999999;
    --icon-dark: #555555;
  }
  * { box-sizing: border-box; margin: 0; padding: 0; }
  html, body { width: 848px; height: 1200px; overflow: hidden; }
  body {
    position: relative;
    background: var(--page-bg);
    font-family: "PT Sans", Arial, sans-serif;
    color: var(--text-dark);
  }

  /* Header */
  .site-header {
    position: absolute; left: 0; top: 0; width: 848px; height: 132px;
    background: var(--panel-bg);
    border-bottom: 1px solid var(--rule);
  }
  .brand {
    position: absolute; left: 70px; top: 82px;
    display: flex; align-items: center; gap: 6px;
  }
  .brand-dot { width: 14px; height: 14px; border-radius: 50%; background: var(--brand-blue); }
  .brand-name {
    font-family: "PT Sans", Arial, sans-serif; font-weight: 700;
    font-size: 17px; letter-spacing: 0.5px; color: var(--brand-blue);
  }
  .welcome {
    position: absolute; right: 71px; top: 12px;
    font-family: "Roboto Slab", Georgia, serif; font-weight: 400;
    font-size: 19px; color: var(--brand-gold);
  }
  .search {
    position: absolute; left: 497px; top: 54px; display: flex; gap: 5px;
  }
  .search-input {
    width: 216px; height: 25px; border: 1px solid #d6d6d6; background: #fff;
    font-size: 10px; color: var(--text-light); padding: 6px 10px; border-radius: 2px;
  }
  .search-button {
    width: 54px; height: 25px; background: var(--accent-yellow);
    border-radius: 2px; font-size: 11px; color: #7a5a00;
    display: flex; align-items: center; justify-content: center;
  }
  .score {
    position: absolute; left: 497px; top: 99px;
    font-size: 11.5px; color: var(--brand-blue);
    display: flex; align-items: center; gap: 6px;
  }
  .account-links {
    position: absolute; right: 76px; top: 99px;
    font-size: 11px; color: var(--text-muted);
  }
  .account-links .sep { margin: 0 6px; }

  /* Timeline */
  .timeline-rail {
    position: absolute; left: 70px; top: 150px; width: 1px; height: 970px;
    background: #cfcfcf;
  }
  .rail-cap { position: absolute; left: 66px; }
  .timeline-item {
    position: absolute; left: 40px; display: flex; align-items: center;
  }
  .timeline-age { width: 27px; text-align: right; font-size: 8px; color: var(--text-light); margin-right: 5px; }
  .timeline-node { width: 13px; height: 13px; margin-right: 10px; }
  .timeline-title {
    font-family: "Roboto Slab", Georgia, serif; font-weight: 300;
    font-size: 16px; color: #555;
  }
  .divider { position: absolute; left: 70px; width: 708px; height: 1px; background: var(--rule); }

  .sort {
    position: absolute; left: 641px; top: 156px; display: flex; align-items: center; gap: 6px;
    font-size: 9px; color: var(--text-muted);
  }
  .sort-select {
    width: 97px; height: 20px; border: 1px solid #cfcfcf; background: #fff;
    font-size: 9px; color: var(--text-dark); padding: 4px 7px;
    display: flex; justify-content: space-between; align-items: center;
  }

  /* Task checklist */
  .task-list {
    position: absolute; left: 93px; top: 260px; width: 172px; height: 258px;
    background: #fff; border: 1px solid #d4d4d4; border-top: none;
    list-style: none; padding: 0 7px;
  }
  .task-list li {
    height: 31px; display: flex; align-items: center; gap: 9px;
    font-size: 11px; color: var(--text-dark); padding-left: 12px;
    border-bottom: 1px solid #ececec;
  }
  .task-list li:last-child { border-bottom: none; }
  .checkbox { width: 9px; height: 9px; border: 1px solid #aaa; background: #f4f4f4; position: relative; }

  /* Related content */
  .related-heading {
    position: absolute; left: 278px; top: 274px;
    font-family: "Roboto Slab", Georgia, serif; font-weight: 400;
    font-size: 14px; color: #444;
  }
  .card-grid {
    position: absolute; left: 278px; top: 310px;
    display: grid; grid-template-columns: 238px 238px; grid-auto-rows: 265px;
    column-gap: 21px; row-gap: 23px;
  }
  .card { background: #fff; border: 1px solid #d4d4d4; padding: 4px; position: relative; }
  .card-media { position: relative; height: 129px; }
  .card-badge {
    position: absolute; right: 2px; bottom: 2px; width: 27px; height: 27px;
    background: var(--accent-yellow); display: flex; align-items: center; justify-content: center;
  }
  .card-title {
    margin: 10px 8px 0; font-family: "Roboto Slab", Georgia, serif; font-weight: 400;
    font-size: 11.5px; line-height: 16px; color: var(--brand-blue);
  }
  .card-rating { margin: 8px 8px 0; display: flex; align-items: center; gap: 1px; font-size: 10px; color: var(--text-muted); }
  .card-rating .count { margin-left: 7px; }
  .card-excerpt { margin: 9px 8px 0; font-size: 9.5px; line-height: 16px; color: var(--text-muted); }
  .read-more { color: var(--brand-blue); white-space: nowrap; margin-left: 3px; }
  .read-more svg { vertical-align: -1px; margin-right: 2px; }

  .media-a { background: linear-gradient(135deg, #8a8d92 0%, #c9cbd0 45%, #3a3c42 100%); }
  .media-b { background: linear-gradient(135deg, #7d6a55 0%, #d8ccbb 50%, #4a3d33 100%); }
  .media-c { background: linear-gradient(135deg, #c4442c 0%, #c99a70 45%, #6b4e36 100%); }
  .media-d { background: linear-gradient(135deg, #3e4045 0%, #8b8d92 50%, #d9835a 75%, #3e4045 100%); }
  .media-e { background: linear-gradient(135deg, #6e7c88 0%, #b9c7d0 50%, #5b6670 100%); }
  .media-f { background: linear-gradient(135deg, #4a3a30 0%, #c8b9ae 50%, #6a5a52 100%); }

  /* Floating share bar */
  .share-bar {
    position: absolute; left: 810px; top: 524px; width: 38px; height: 152px;
    background: var(--brand-blue); border-radius: 3px 0 0 3px;
    display: flex; flex-direction: column; align-items: center; justify-content: space-around;
    padding: 8px 0;
  }
  .share-dot { width: 18px; height: 18px; border-radius: 50%; background: #fff; }

  .footer-rule { position: absolute; left: 0; top: 1198px; width: 848px; height: 1px; background: var(--rule); }
</style>
</head>
<body>
<svg width="0" height="0" style="position:absolute">
  <defs>
    <symbol id="star" viewBox="0 0 20 20">
      <polygon points="10,1 12.6,7 19,7.5 14,11.8 15.6,18.5 10,15 4.4,18.5 6,11.8 1,7.5 7.4,7" fill="#f5b820"/>
    </symbol>
    <symbol id="star-half" viewBox="0 0 20 20">
      <polygon points="10,1 12.6,7 19,7.5 14,11.8 15.6,18.5 10,15 4.4,18.5 6,11.8 1,7.5 7.4,7" fill="none" stroke="#f5b820" stroke-width="1.4"/>
      <polygon points="10,1 10,15 4.4,18.5 6,11.8 1,7.5 7.4,7" fill="#f5b820"/>
    </symbol>
    <symbol id="doc" viewBox="0 0 16 16">
      <rect x="3" y="2" width="10" height="12" rx="1" fill="#1a1a1a"/>
      <rect x="5" y="4" width="6" height="1" fill="#f5c42a"/>
    </symbol>
    <symbol id="cart" viewBox="0 0 16 16">
      <path d="M1 3h2.5l2 7h7.5l1.5-5H4.5" fill="none" stroke="#1a1a1a" stroke-width="1.4"/>
      <circle cx="6.5" cy="12.5" r="1.2" fill="#1a1a1a"/>
      <circle cx="12" cy="12.5" r="1.2" fill="#1a1a1a"/>
    </symbol>
    <symbol id="plus-dot" viewBox="0 0 10 10">
      <circle cx="5" cy="5" r="5" fill="#434aa9"/>
      <path d="M5 2.5v5M2.5 5h5" stroke="#fff" stroke-width="1.3"/>
    </symbol>
  </defs>
</svg>

<header class="site-header">
  <div class="brand"><span class="brand-dot"></span><span class="brand-name">DADHARBOR</span></div>
  <p class="welcome">Welcome Greg, what would you like to do today?</p>
  <div class="search">
    <div class="search-input">Keyword...</div>
    <div class="search-button">SEARCH</div>
  </div>
  <p class="score">
    <svg width="10" height="9" viewBox="0 0 10 9"><path d="M5 9L.8 4.6A2.4 2.4 0 0 1 5 1.3a2.4 2.4 0 0 1 4.2 3.3z" fill="#434aa9"/></svg>
    Super Dad Score: 10,500
  </p>
  <p class="account-links">My Account<span class="sep">|</span>Log out</p>
</header>

<div class="timeline-rail"></div>
<svg class="rail-cap" style="top:145px" width="9" height="6" viewBox="0 0 9 6"><path d="M1 5l3.5-4 3.5 4" fill="none" stroke="#bbb" stroke-width="1.2"/></svg>
<svg class="rail-cap" style="top:1116px" width="9" height="6" viewBox="0 0 9 6"><path d="M1 1l3.5 4 3.5-4" fill="none" stroke="#bbb" stroke-width="1.2"/></svg>

<div class="timeline-item" style="top:158px">
  <span class="timeline-age">-3 mo</span>
  <svg class="timeline-node" viewBox="0 0 13 13"><circle cx="6.5" cy="6.5" r="6.5" fill="#555"/><path d="M3.5 6.5h6M7 4l2.5 2.5L7 9" fill="none" stroke="#fff" stroke-width="1.4"/></svg>
  <span class="timeline-title">Prepare for the baby arrival</span>
</div>
<div class="sort">Sort by :<div class="sort-select">Most recent<svg width="7" height="4" viewBox="0 0 7 4"><path d="M0 0h7L3.5 4z" fill="#555"/></svg></div></div>
<div class="divider" style="top:200px"></div>

<div class="timeline-item" style="top:218px">
  <span class="timeline-age">0 mo</span>
  <svg class="timeline-node" viewBox="0 0 13 13"><circle cx="6.5" cy="6.5" r="6.5" fill="#555"/><path d="M9.5 6.5h-6M6 4L3.5 6.5 6 9" fill="none" stroke="#fff" stroke-width="1.4"/></svg>
  <span class="timeline-title">What’s the Latest?</span>
</div>
<div class="divider" style="top:260px"></div>

<ul class="task-list">
  <li><span class="checkbox"></span>Buy a crib</li>
  <li><span class="checkbox"></span>Assemble the crib</li>
  <li><span class="checkbox"></span>Buy a stroller</li>
  <li><span class="checkbox"><svg style="position:absolute;left:0;top:-1px" width="9" height="9" viewBox="0 0 9 9"><path d="M1.5 4.5l2 2 4-5" fill="none" stroke="#434aa9" stroke-width="1.4"/></svg></span>Buy a carseat</li>
  <li><span class="checkbox"></span>Install a carseat</li>
  <li><span class="checkbox"></span>Learn to change a diaper</li>
  <li><span class="checkbox"></span>Learn to hold a baby</li>
  <li><span class="checkbox"></span>Set a fedding schedule</li>
</ul>

<div class="timeline-item" style="top:551px">
  <span class="timeline-age">0 mo</span>
  <svg class="timeline-node" viewBox="0 0 13 13"><circle cx="6.5" cy="6.5" r="6.5" fill="#555"/><path d="M3.5 6.5h6M7 4l2.5 2.5L7 9" fill="none" stroke="#fff" stroke-width="1.4"/></svg>
  <span class="timeline-title">What you searched for</span>
</div>

<h2 class="related-heading">Related milestones and tasks include</h2>

<section class="card-grid">
  <article class="card">
    <div class="card-media media-a" role="img" aria-label="Photo of a baby in a car seat reaching for a hanging toy">
      <span class="card-badge"><svg width="16" height="16"><use href="#doc"/></svg></span>
    </div>
    <h3 class="card-title">Pellentesque habitant morbi tristique senectus et netus</h3>
    <div class="card-rating"><svg width="12" height="12"><use href="#star"/></svg><svg width="12" height="12"><use href="#star"/></svg><svg width="12" height="12"><use href="#star"/></svg><svg width="12" height="12"><use href="#star"/></svg><svg width="12" height="12"><use href="#star-half"/></svg><span class="count">3,121 ratings</span></div>
    <p class="card-excerpt">I went out to buy my first car seat and had to earn my PhD in car seats, Newtonian physics, and anti-stain technology… <span class="read-more"><svg width="9" height="9"><use href="#plus-dot"/></svg>Read More</span></p>
  </article>
  <article class="card">
    <div class="card-media media-b" role="img" aria-label="Photo of a smiling baby in an infant carrier">
      <span class="card-badge"><svg width="16" height="16"><use href="#cart"/></svg></span>
    </div>
    <h3 class="card-title">Pellentesque habitant morbi tristique senectus et netus</h3>
    <div class="card-rating"><svg width="12" height="12"><use href="#star"/></svg><svg width="12" height="12"><use href="#star"/></svg><svg width="12" height="12"><use href="#star"/></svg><svg width="12" height="12"><use href="#star"/></svg><svg width="12" height="12"><use href="#star-half"/></svg><span class="count">3,121 ratings</span></div>
    <p class="card-excerpt">I went out to buy my first car seat and had to earn my PhD in car seats, Newtonian physics, and anti-stain technology… <span class="read-more"><svg width="9" height="9"><use href="#plus-dot"/></svg>Read More</span></p>
  </article>
  <article class="card">
    <div class="card-media media-c" role="img" aria-label="Photo of a toddler buckled into a car seat">
      <span class="card-badge"><svg width="16" height="16"><use href="#doc"/></svg></span>
    </div>
    <h3 class="card-title">Pellentesque habitant morbi tristique senectus et netus</h3>
    <div class="card-rating"><svg width="12" height="12"><use href="#star"/></svg><svg width="12" height="12"><use href="#star"/></svg><svg width="12" height="12"><use href="#star"/></svg><svg width="12" height="12"><use href="#star"/></svg><svg width="12" height="12"><use href="#star-half"/></svg><span class="count">3,121 ratings</span></div>
    <p class="card-excerpt">I went out to buy my first car seat and had to earn my PhD in car seats, Newtonian physics, and anti-stain technology… <span class="read-more"><svg width="9" height="9"><use href="#plus-dot"/></svg>Read More</span></p>
  </article>
  <article class="card">
    <div class="card-media media-d" role="img" aria-label="Photo of a baby strapped into a dark infant seat">
      <span class="card-badge"><svg width="16" height="16"><use href="#cart"/></svg></span>
    </div>
    <h3 class="card-title">Pellentesque habitant morbi tristique senectus et netus</h3>
    <div class="card-rating"><svg width="12" height="12"><use href="#star"/></svg><svg width="12" height="12"><use href="#star"/></svg><svg width="12" height="12"><use href="#star"/></svg><svg width="12" height="12"><use href="#star"/></svg><svg width="12" height="12"><use href="#star-half"/></svg><span class="count">3,121 ratings</span></div>
    <p class="card-excerpt">I went out to buy my first car seat and had to earn my PhD in car seats, Newtonian physics, and anti-stain technology… <span class="read-more"><svg width="9" height="9"><use href="#plus-dot"/></svg>Read More</span></p>
  </article>
  <article class="card">
    <div class="card-media media-e" role="img" aria-label="Photo of a baby under a car seat belt">
      <span class="card-badge"><svg width="16" height="16"><use href="#doc"/></svg></span>
    </div>
    <h3 class="card-title">Pellentesque habitant morbi tristique senectus et netus</h3>
    <div class="card-rating"><svg width="12" height="12"><use href="#star"/></svg><svg width="12" height="12"><use href="#star"/></svg><svg width="12" height="12"><use href="#star"/></svg><svg width="12" height="12"><use href="#star"/></svg><svg width="12" height="12"><use href="#star-half"/></svg><span class="count">3,121 ratings</span></div>
    <p class="card-excerpt">I went out to buy my first car seat and had to earn my PhD in car seats, Newtonian physics, and anti-stain technology… <span class="read-more"><svg width="9" height="9"><use href="#plus-dot"/></svg>Read More</span></p>
  </article>
  <article class="card">
    <div class="card-media media-f" role="img" aria-label="Photo of a sleeping newborn in a car seat">
      <span class="card-badge"><svg width="16" height="16"><use href="#cart"/></svg></span>
    </div>
    <h3 class="card-title">Pellentesque habitant morbi tristique senectus et netus</h3>
    <div class="card-rating"><svg width="12" height="12"><use href="#star"/></svg><svg width="12" height="12"><use href="#star"/></svg><svg width="12" height="12"><use href="#star"/></svg><svg width="12" height="12"><use href="#star"/></svg><svg width="12" height="12"><use href="#star-half"/></svg><span class="count">3,121 ratings</span></div>
    <p class="card-excerpt">I went out to buy my first car seat and had to earn my PhD in car seats, Newtonian physics, and anti-stain technology… <span class="read-more"><svg width="9" height="9"><use href="#plus-dot"/></svg>Read More</span></p>
  </article>
</section>

<nav class="share-bar" aria-label="Share">
  <span class="share-dot"></span>
  <span class="share-dot"></span>
  <span class="share-dot"></span>
  <span class="share-dot"></span>
</nav>

<div class="footer-rule"></div>
</body>
</html>
```